New Webpage for High Class Expert Witness Services Company

We are looking for a minimalist design for a webpage that just has our logo and an entry form offer to connect with one of our Liaisons.
The entry form should just ask for Name, Email, Contact Info and Description of Project.

Company Name is: The Marlowe Crest Advisory Services

Number of Pages Required

1 page

```html
<!DOCTYPE html>
<html lang="en">
<head>
<meta charset="UTF-8">
<title>The Marlowe Crest Advisory Services — Request Consultation</title>
<link href="https://fonts.googleapis.com/css2?family=Cinzel:wght@400;700&family=Questrial&family=Urbanist:wght@300;700&family=Figtree:wght@400&display=swap" rel="stylesheet">
<style>
  :root {
    --bg-base: #111111;
    --bg-panel: #191919;
    --bg-corner: #0c0c0c;
    --text-main: #f2f2f2;
    --text-soft: #dadada;
    --text-accent: #9a9a9a;
    --card-top: #1a1a1a;
    --card-bottom: #232323;
    --card-edge: #3a3a3a;
    --field: #dcdcdc;
    --button: #6b5530;
    --rule: #555555;
  }
  * { box-sizing: border-box; margin: 0; padding: 0; }
  html, body { width: 1200px; height: 675px; overflow: hidden; }
  body {
    position: relative;
    background: var(--bg-base);
    color: var(--text-main);
    font-family: "Figtree", sans-serif;
  }
  .backdrop { position: absolute; inset: 0; width: 1200px; height: 675px; }

  .brand {
    position: absolute; top: 36px; left: 0; width: 1200px;
    display: flex; justify-content: center; align-items: center; gap: 12px;
  }
  .brand-mark { width: 26px; height: 26px; background: var(--text-soft); }
  .brand-name {
    font-family: "Cinzel", serif; font-weight: 400; color: var(--text-soft);
    text-align: center; line-height: 1.1;
  }
  .brand-name .line-1 { display: block; font-size: 23px; letter-spacing: 1px; }
  .brand-name .line-2 { display: block; font-size: 12px; letter-spacing: 4px; margin-top: 3px; }

  .headline {
    position: absolute; top: 104px; left: 0; width: 1200px; text-align: center;
    font-family: "Cinzel", serif; font-weight: 400; font-size: 31px;
    line-height: 37px; letter-spacing: 2px; color: var(--text-main);
  }
  .headline strong { font-weight: 700; color: var(--text-accent); text-transform: uppercase; }
  .tagline {
    position: absolute; top: 188px; left: 0; width: 1200px; text-align: center;
    font-family: "Questrial", sans-serif; font-size: 16px; letter-spacing: 1.2px;
    color: var(--text-soft);
  }

  .consult-card {
    position: absolute; left: 424px; top: 228px; width: 352px; height: 412px;
    border-radius: 24px; border: 1px solid var(--card-edge);
    background: linear-gradient(180deg, var(--card-top), var(--card-bottom));
  }
  .card-title {
    margin-top: 20px; text-align: center;
    font-family: "Urbanist", sans-serif; font-weight: 300; font-size: 23px; color: var(--text-main);
  }
  .card-title strong { font-weight: 700; color: var(--text-accent); }
  .card-rule {
    width: 172px; height: 1px; margin: 13px auto 0;
    background: linear-gradient(90deg, transparent, var(--rule), transparent);
  }
  .consult-form { width: 225px; margin: 10px auto 0; }
  .field-label { display: block; font-size: 11px; color: var(--text-main); margin: 0 0 4px; }
  .field-input {
    display: block; width: 224px; height: 34px; margin: 0 0 8px 1px;
    border: none; border-radius: 2px; background: var(--field);
  }
  .field-input.is-long { height: 86px; resize: none; }
  .submit-button {
    display: block; width: 225px; height: 34px; margin-top: 3px;
    border: none; border-radius: 2px; background: var(--button);
    color: var(--text-main); font-family: "Figtree", sans-serif; font-size: 11px;
  }
</style>
</head>
<body>
  <svg class="backdrop" viewBox="0 0 1200 675" aria-hidden="true">
    <path d="M238 675 L296 380 Q305 330 345 305 L806 0 L1200 0 L1200 675 Z" fill="var(--bg-panel)"/>
    <path d="M846 0 L1200 0 L1200 675 L846 675 Z" fill="#141414"/>
    <path d="M866 0 L1200 0 L1200 218 Z" fill="var(--bg-corner)"/>
  </svg>

  <header class="brand">
    <span class="brand-mark"></span>
    <span class="brand-name">
      <span class="line-1">MARLOWE CREST</span>
      <span class="line-2">ADVISORY SERVICES</span>
    </span>
  </header>

  <h1 class="headline">When the stakes are <strong>absolute,</strong><br>the standard must be too.</h1>
  <p class="tagline">Expert witness integration &amp; legal defense support</p>

  <section class="consult-card">
    <h2 class="card-title">Tell us about Your <strong>Matter</strong></h2>
    <div class="card-rule"></div>
    <form class="consult-form">
      <label class="field-label" for="full-name">Full Name</label>
      <input class="field-input" id="full-name" type="text">
      <label class="field-label" for="email">Email</label>
      <input class="field-input" id="email" type="email">
      <label class="field-label" for="phone">Contact Number</label>
      <input class="field-input" id="phone" type="tel">
      <label class="field-label" for="project">Description of Project</label>
      <textarea class="field-input is-long" id="project"></textarea>
      <button class="submit-button" type="button">Request Consultation</button>
    </form>
  </section>
</body>
</html>
```